Webdesign für Hersteller für Pack- und Palettieranlagen für den Getränke- und Lebensmittelbereich
Webdesign für Hersteller für Pack- und Palettieranlagen für den Getränke- und Lebensmittelbere..
Zielgruppe
Hersteller für Pack- und Palettieranlagen für den Getränke- und Lebensmittelbereich
Zielgruppe: Getränke- und Lebensmittelhersteller
Aufgabenstellung
die zukünftige Seite soll dynamischer und intuitiver werden
klare Strukturen, aber morderner als das jetztige Layout
Keine Kopie der alten Seite www.kolmatech.de!
Startseite soll aufgeräumter sein
Logo, Rufnummer, Mail, Social Media
Startseite mit großem Headerbild (Slider)

```html
<!DOCTYPE html>
<html lang="de">
<head>
<meta charset="utf-8">
<title>KOLMATECH Maschinenbau GmbH</title>
<link href="https://fonts.googleapis.com/css2?family=Poppins:wght@300;400;500;700&display=swap" rel="stylesheet">
<style>
:root{
  --green:#6ab42d;
  --green-dark:#4f8f1c;
  --text:#222;
  --muted:#555;
  --light:#f6f6f6;
  --white:#fff;
}
*{box-sizing:border-box;margin:0;padding:0}
html,body{width:1200px;height:3062px;overflow:hidden}
body{position:relative;font-family:'Poppins',sans-serif;color:var(--text);background:var(--light)}
.abs{position:absolute}
.photo{position:absolute}
.hero{left:0;top:0;width:1200px;height:593px;background:linear-gradient(100deg,#b9bfc4 0%,#d8dde0 35%,#9ea6ad 65%,#6f777e 100%)}
.topbar{left:106px;top:8px;width:987px;height:20px;color:#fff;font-size:13px;display:flex;align-items:center;gap:20px}
.topbar span{display:flex;align-items:center;gap:5px}
.social{position:absolute;right:0;top:0;display:flex;gap:7px}
.social i{width:18px;height:18px;border-radius:50%;background:#fff;display:block}
.nav{left:106px;top:38px;width:987px;height:49px;background:#fff;display:flex;align-items:center;padding:0 18px}
.brand{display:flex;align-items:center;gap:6px;font-weight:700;color:var(--green);font-size:17px;line-height:1}
.brand i{width:14px;height:14px;border-radius:50%;background:var(--green);display:block}
.nav ul{list-style:none;display:flex;gap:22px;margin-left:auto;font-size:11px}
.nav li.active{color:var(--green)}
.nav li.under{border-bottom:2px solid var(--green);padding-bottom:4px;margin-bottom:-6px}
.claim{left:194px;top:538px;width:530px;height:98px;background:var(--green);color:#fff;font-size:19px;line-height:1.2;padding:28px 32px}
.badges{left:724px;top:538px;width:282px;height:98px;background:#fff;display:flex;align-items:center;gap:20px;padding:0 30px}
.badges i{display:block;background:#dfe4ec;height:36px}
.prod-title{left:122px;top:686px;font-size:40px;color:var(--green);font-weight:300;line-height:1.1;white-space:nowrap}
.prod-sep{left:453px;top:691px;width:1px;height:38px;background:var(--green)}
.prod-lead{left:480px;top:700px;font-size:14px}
.card{position:absolute;background:#fff;text-align:center;padding-top:20px}
.card h3{font-size:16px;font-weight:400;color:var(--green);margin-bottom:4px}
.card p{font-size:12px;line-height:1.3}
.btn{display:inline-block;background:var(--green);color:#fff;font-size:13px;padding:8px 20px;margin-top:38px}
.outline{left:494px;top:1169px;width:211px;height:47px;border:1px solid var(--green);color:var(--green);font-size:17px;display:flex;align-items:center;justify-content:center;background:transparent}
.news{left:0;top:1269px;width:1200px;height:537px;background:#fff}
.sec-title{position:absolute;left:0;width:1200px;text-align:center;color:var(--green);font-size:43px;font-weight:400}
.sec-sub{position:absolute;left:0;width:1200px;text-align:center;font-size:16px}
.ncard{position:absolute;top:1413px;width:250px;height:255px;background:var(--light)}
.ncard .img{height:149px}
.ncard h4{font-size:11.5px;font-weight:400;color:var(--green);padding:18px 20px 4px;line-height:1.3}
.ncard p{font-size:8.5px;color:var(--muted);padding:0 20px;line-height:1.35}
.more{left:532px;top:1700px;width:136px;height:47px;background:var(--green);color:#fff;font-size:17px;display:flex;align-items:center;justify-content:center}
.jobs{left:0;top:1806px;width:1200px;height:438px;background:linear-gradient(90deg,#c9c9c9 0%,#f1f1f1 30%,#f8f8f8 70%,#eee 100%)}
.video{left:380px;top:1944px;width:438px;height:245px;background:linear-gradient(180deg,#5d5448,#3a4a6b 60%,#2c3a5c)}
.video .play{position:absolute;left:204px;top:110px;width:30px;height:30px;border-radius:50%;background:rgba(0,0,0,.55)}
.video .play:after{content:"";position:absolute;left:12px;top:9px;border-left:9px solid #fff;border-top:6px solid transparent;border-bottom:6px solid transparent}
.video .bar{position:absolute;left:0;bottom:0;width:100%;height:12px;background:#111}
.about{left:0;top:2244px;width:1200px;height:562px;background:linear-gradient(90deg,#3d7a12,#5da123 40%,#4c8c1a 70%,#2f6410)}
.about-box{left:0;top:2331px;width:530px;height:387px;background:#fff;padding:36px 44px 0 110px}
.about-box h2{font-size:42px;font-weight:400;color:var(--green);line-height:1.1}
.about-box .lead{font-size:13px;line-height:1.2;margin-bottom:18px}
.about-box h3{font-size:19px;font-weight:400;color:var(--green);margin-bottom:14px}
.about-box p{font-size:8.4px;color:var(--muted);line-height:1.35;margin-bottom:9px}
.footer{left:0;top:2806px;width:1200px;height:208px;background:var(--light)}
.fcol{position:absolute;top:2850px;font-size:10.5px;line-height:1.45;color:var(--muted)}
.fcol h4{font-size:22px;font-weight:400;color:var(--green);margin-bottom:12px}
.ficons{display:flex;gap:7px;margin-top:14px}
.ficons i{width:18px;height:18px;border-radius:50%;background:var(--green);display:block}
.copy{left:0;top:3014px;width:1200px;height:48px;border-top:1px solid #e2e2e2;font-size:7.5px;color:var(--muted);display:flex;align-items:center;justify-content:center;background:var(--light)}
</style>
</head>
<body>

<div class="photo hero" role="img" aria-label="Techniker in Schutzkleidung an einem Edelstahltank in der Produktion"></div>
<div class="abs topbar">
  <span><svg width="12" height="12" viewBox="0 0 24 24" fill="none" stroke="#fff" stroke-width="2"><path d="M5 3h4l2 5-3 2a11 11 0 0 0 6 6l2-3 5 2v4a2 2 0 0 1-2 2A18 18 0 0 1 3 5a2 2 0 0 1 2-2z"/></svg>030 4471 / 220 - 0</span>
  <span><svg width="13" height="11" viewBox="0 0 24 18" fill="none" stroke="#fff" stroke-width="2"><rect x="1" y="1" width="22" height="16"/><path d="M1 1l11 9 11-9"/></svg>info@kolmatech.de</span>
  <div class="social"><i></i><i></i><i></i><i></i><i></i></div>
</div>
<div class="abs nav">
  <div class="brand"><i></i>KOLMATECH</div>
  <ul>
    <li class="active">Unternehmen</li><li class="under">Jobs / Karriere</li><li>Palettiertechnik</li><li>Packertechnik</li><li>Fördertechnik</li><li>Anlagen</li><li>Gebrauchtmaschinen</li><li>Aktuelles</li>
  </ul>
</div>
<div class="abs claim">Qualität, die überzeugt durch mehr als <b>155 Jahre Tradition</b>, Geschichte und Erfahrung.</div>
<div class="abs badges"><i style="width:80px"></i><i style="width:118px"></i></div>

<h2 class="abs prod-title">Unsere Produkte</h2>
<div class="abs prod-sep"></div>
<p class="abs prod-lead">Erfahren Sie mehr über unsere Produkte.Wählen Sie eine Kategorie:</p>

<div class="card" style="left:125px;top:762px;width:225px;height:169px"><h3>Fördertechnik</h3><p>FlowLine<br>Behälter- und Gebindetransport</p><span class="btn">Mehr dazu</span></div>
<div class="photo" style="left:125px;top:931px;width:225px;height:194px;background:linear-gradient(135deg,#5a4a32,#b9a88a 45%,#40382c)" role="img" aria-label="Glasflaschen in einer Abfüllanlage"></div>
<div class="card" style="left:375px;top:762px;width:225px;height:169px"><h3>Gebrauchtmaschinen</h3><p>StackLine<br>Unsere Palettierfamilie</p><span class="btn">Mehr dazu</span></div>
<div class="photo" style="left:375px;top:931px;width:225px;height:194px;background:linear-gradient(135deg,#2f6fa8,#a9d0ee 45%,#3d7fb8)" role="img" aria-label="Schaltschrank mit Leuchttastern und Rohrleitungen"></div>
<div class="card" style="left:624px;top:762px;width:225px;height:169px"><h3>Palettiertechnik</h3><p>StackLine<br>Unsere Palettierfamilie</p><span class="btn" style="margin-top:33px">Mehr dazu</span></div>
<div class="photo" style="left:849px;top:762px;width:225px;height:169px;background:linear-gradient(135deg,#cfd6d4,#6f8a7c 50%,#2f6f3a)" role="img" aria-label="Grüne Glasflaschen auf einem Transportband"></div>
<div class="card" style="left:624px;top:956px;width:225px;height:169px"><h3>Packertechnik</h3><p>PackLine<br>unsere Flaschenpacker</p><span class="btn" style="margin-top:33px">Mehr dazu</span></div>
<div class="photo" style="left:849px;top:956px;width:225px;height:169px;background:linear-gradient(135deg,#c96a2a,#2a3f7a 50%,#a9b5c8)" role="img" aria-label="Greiferköpfe eines Flaschenpackers"></div>
<div class="abs outline">Alle Produkte anzeigen</div>

<div class="abs news"></div>
<h2 class="sec-title" style="top:1300px">Aktuelles</h2>
<p class="sec-sub" style="top:1355px">Termine und aktuelle Meldungen</p>
<svg class="abs" style="left:106px;top:1481px" width="43" height="20" viewBox="0 0 43 20" fill="none" stroke="#6ab42d" stroke-width="1.5"><path d="M43 10H2M11 1L2 10l9 9"/></svg>
<svg class="abs" style="left:1050px;top:1481px" width="43" height="20" viewBox="0 0 43 20" fill="none" stroke="#6ab42d" stroke-width="1.5"><path d="M0 10h41M32 1l9 9-9 9"/></svg>
<div class="ncard" style="left:188px"><div class="img" style="background:linear-gradient(135deg,#8a8f92,#b5541e 45%,#5a3010)" role="img" aria-label="Braune Flaschen in einer Abfüllanlage"></div><h4>Neue Abfüllanlage für Brunnhof Limo</h4><p>Der traditionsreiche Limonadenhersteller Brunnhof Limo aus der Oberlausitz investierte 2022/23 in eine neue Abfüllanlage…</p></div>
<div class="ncard" style="left:474px"><div class="img" style="background:linear-gradient(135deg,#cfd6d4,#6f8a7c 50%,#2f6f3a)" role="img" aria-label="Grüne Glasflaschen auf einem Transportband"></div><h4>Erneuerung Glasabfüllanlage Molkereigenossenschaft Talwiesen</h4><p>Die Molkereigenossenschaft Talwiesen erneuerte von 2020 bis 2022 in mehreren Bauabschnitten die Abfüllanlage für…</p></div>
<div class="ncard" style="left:762px"><div class="img" style="background:linear-gradient(135deg,#7d858c,#cfd4d8 50%,#5b6168)" role="img" aria-label="Techniker zwischen Edelstahltanks"></div><h4>Neue Abfüllanlage für Brunnhof Limo</h4><p>Der traditionsreiche Limonadenhersteller Brunnhof Limo aus der Oberlausitz investierte 2022/23 in eine neue Abfüllanlage…</p></div>
<div class="abs more">Mehr lesen</div>

<div class="photo jobs" role="img" aria-label="Maschinenflansch in Graustufen als Hintergrund"></div>
<h2 class="sec-title" style="top:1845px">Jobs &amp; Karriere</h2>
<p class="sec-sub" style="top:1901px">Werden Sie Teil unseres Teams.</p>
<div class="abs video" role="img" aria-label="Video mit drei Mitarbeitern in Arbeitskleidung in der Lagerhalle"><div class="play"></div><div class="bar"></div></div>

<div class="photo about" role="img" aria-label="Techniker in Schutzkleidung an einem Tank, grün eingefärbt"></div>
<div class="abs about-box">
  <h2>Über uns</h2>
  <p class="lead">Qualität, die überzeugt durch mehr als 155 Jahre Tradition, Geschichte und Erfahrung.</p>
  <h3>KOLMATECH Maschinenbau GmbH</h3>
  <p>Wir sind ein Unternehmen mit einer über einhundertjährigen Geschichte. Gegründet im Jahre 1862 als Metallwarenfirma, wird die Firma heute in der vierten Generation weitergeführt und mit viel persönlichem Engagement ausgebaut.</p>
  <p>Sowohl räumlich, inzwischen stehen für die Produktion mehr als 2.500 m² zur Verfügung, als auch produktseitig haben wir gerade in den letzten Jahren viel investiert. Dadurch stehen unseren Kunden beste Voraussetzungen zur Verfügung, um alle Problemstellungen optimal zu lösen.</p>
  <p>Mit einer hohen Fertigungstiefe stellen wir Förder- und Verpackungstechnik von der einzelnen Maschine bis zur kompletten Anlage her.</p>
  <p>Gerne nehmen wir Ihre Problemstellungen in einem persönlichen Gespräch entgegen.</p>
  <p>Mehr über die KOLMATECH Maschinenbau GmbH erfahren sie hier.</p>
</div>

<div class="abs footer"></div>
<div class="fcol" style="left:106px"><h4>Quicklinks</h4>Startseite<br>Nternehmen<br>Downloads<br>Medien-Center<br>Presse</div>
<div class="fcol" style="left:274px;top:2885px">Aktuelles<br>Jobs &amp; Karriere<br>Kontakt</div>
<div class="fcol" style="left:455px"><h4>Produkte</h4>Palettiertechnik<br>Packertechnik<br>Fördertechnik<br>Anlagen<br>Gebrauchtmaschinen</div>
<div class="fcol" style="left:680px"><h4>Kontakt</h4>KOLMATECH Maschinenbau GmbH<br>Am Werkhof 12<br>09112 Chemnitz<div class="ficons"><i></i><i></i><i></i><i></i><i></i></div></div>
<div class="fcol" style="left:898px"><div class="brand" style="margin:2px 0 16px">KOLMATECH<i></i></div>Telefon: 030 4471 / 220 - 0<br>Fax: 030 4471 / 220 - 14<br>E-Mail: info@kolmatech.de</div>
<div class="abs copy">2024 © KOLMATECH Maschinenbau GmbH | Datenschutz Impressum</div>

</body>
</html>
```